Frostvale Harborline LLC

we need a business card design

Industry/Entity Type

hvac

Contact Information for Business Card

my logo

Requirements
Must have
• my logo and same colors

```html
<!DOCTYPE html>
<html lang="en">
<head>
<meta charset="UTF-8">
<title>Frostvale Harborline LLC – Business Card</title>
<link href="https://fonts.googleapis.com/css2?family=Montserrat:wght@400;500;700;800&display=swap" rel="stylesheet">
<style>
  :root {
    --brand-blue: #0f5fa8;
    --deep-blue: #0d56a0;
    --sky-blue: #18a6e0;
    --gold: #f2b84b;
    --ink: #3a3a3a;
    --paper: #ffffff;
    --backdrop: #2b2b2b;
  }
  * { box-sizing: border-box; margin: 0; padding: 0; }
  html, body {
    width: 1200px; height: 875px; overflow: hidden;
    background: var(--backdrop);
    font-family: "Montserrat", Arial, sans-serif;
  }
  .stage {
    width: 1200px; height: 875px;
    display: flex; flex-direction: column; align-items: center; justify-content: center;
    gap: 40px;
  }
  .card {
    width: 680px; height: 388px; border-radius: 22px;
    position: relative; overflow: hidden;
    box-shadow: 0 14px 30px rgba(0,0,0,.45);
  }
  /* Front */
  .card-front {
    background: var(--brand-blue);
    display: flex; align-items: center; justify-content: center;
  }
  .brand-mark {
    display: flex; align-items: center; gap: 16px;
    color: var(--paper); font-weight: 800; font-size: 34px; letter-spacing: .5px;
  }
  .brand-dot { width: 26px; height: 26px; border-radius: 50%; background: var(--gold); }
  /* Back */
  .card-back { background: var(--paper); }
  .back-brand {
    position: absolute; top: 44px; right: 44px;
    color: var(--brand-blue); font-weight: 800; font-size: 22px;
  }
  .divider {
    position: absolute; left: 44px; right: 44px; top: 200px;
    height: 1.5px; background: var(--gold);
  }
  .address {
    position: absolute; right: 44px; top: 118px; text-align: right;
    color: var(--ink); font-size: 15px; line-height: 1.45;
  }
  .person { position: absolute; left: 44px; top: 136px; }
  .person-name { font-size: 28px; font-weight: 700; color: var(--deep-blue); letter-spacing: .3px; }
  .person-name .surname { color: var(--sky-blue); }
  .person-role { font-size: 15px; color: var(--ink); margin-top: 2px; }
  .contacts { position: absolute; left: 44px; top: 222px; list-style: none; }
  .contacts li {
    display: flex; align-items: center; gap: 12px;
    font-size: 16px; color: var(--ink); margin-bottom: 9px;
  }
  .contacts svg { width: 16px; height: 16px; fill: var(--sky-blue); flex: none; }
  .stripe { position: absolute; left: 0; bottom: 0; width: 680px; height: 22px; }
</style>
</head>
<body>
<main class="stage">
  <section class="card card-front">
    <div class="brand-mark"><span class="brand-dot"></span>Frostvale Harborline LLC</div>
  </section>

  <section class="card card-back">
    <div class="back-brand">Frostvale Harborline LLC</div>
    <div class="address">12 Quarry Lane<br>Ellisford ABC 4410</div>
    <div class="person">
      <div class="person-name">DORIAN <span class="surname">WELLES</span></div>
      <div class="person-role">Founder</div>
    </div>
    <div class="divider"></div>
    <ul class="contacts">
      <li>
        <svg viewBox="0 0 24 24"><path d="M6.6 10.8a15.1 15.1 0 0 0 6.6 6.6l2.2-2.2a1 1 0 0 1 1-.25 11.4 11.4 0 0 0 3.6.57 1 1 0 0 1 1 1V20a1 1 0 0 1-1 1A17 17 0 0 1 3 4a1 1 0 0 1 1-1h3.5a1 1 0 0 1 1 1c0 1.25.2 2.45.57 3.6a1 1 0 0 1-.25 1z"/></svg>
        555.014.0277
      </li>
      <li>
        <svg viewBox="0 0 24 24"><path d="M2 5h20v14H2zm2 2v.4l8 5 8-5V7zm0 2.8V17h16V9.8l-8 5z"/></svg>
        info@frostvaleharborline.com
      </li>
      <li>
        <svg viewBox="0 0 24 24"><path d="M12 2a10 10 0 1 0 0 20 10 10 0 0 0 0-20zm6.9 9h-3a15 15 0 0 0-1.3-6A8 8 0 0 1 18.9 11zM12 4.1c.9 1.2 1.7 3.6 1.9 6.9h-3.8c.2-3.3 1-5.7 1.9-6.9zM9.4 5a15 15 0 0 0-1.3 6h-3A8 8 0 0 1 9.4 5zm-4.3 8h3a15 15 0 0 0 1.3 6A8 8 0 0 1 5.1 13zm6.9 6.9c-.9-1.2-1.7-3.6-1.9-6.9h3.8c-.2 3.3-1 5.7-1.9 6.9zm2.6-.9a15 15 0 0 0 1.3-6h3a8 8 0 0 1-4.3 6z"/></svg>
        www.frostvaleharborline.com
      </li>
    </ul>
    <svg class="stripe" viewBox="0 0 680 22" preserveAspectRatio="none" aria-hidden="true">
      <polygon points="0,12 300,12 292,22 0,22" fill="var(--deep-blue)"/>
      <polygon points="306,0 560,0 548,22 294,22" fill="var(--sky-blue)"/>
      <polygon points="566,0 680,0 680,22 554,22" fill="var(--gold)"/>
    </svg>
  </section>
</main>
</body>
</html>
```